Business Cards for a law firm

Business cards for our law firm. Use our silhoette logo and OAK PARTNERS - check our website (www.oakpartners.example)

Contact Information for Business Card

our silhouette logo, OAK PARTNERS, 800-555-0147, Dorian Pemberton, dorian@oakpartners.example

Requirements
Must have
• our silhouette logo, OAK PARTNERS, 800-555-0147, Dorian Pemberton, dorian@oakpartners.example

```html
<!DOCTYPE html>
<html lang="en">
<head>
<meta charset="utf-8">
<title>Oak Partners — Business Cards</title>
<link rel="stylesheet" href="https://fonts.googleapis.com/css2?family=Montserrat:wght@400;500;700;800&display=swap">
<style>
  :root {
    --navy: #2b3664;
    --navy-deep: #1f2850;
    --navy-soft: #4a5890;
    --gold: #f7a81b;
    --white: #ffffff;
    --stage: #1b1b1d;
  }
  * { box-sizing: border-box; margin: 0; padding: 0; }
  html, body { width: 1200px; height: 927px; overflow: hidden; }
  body {
    background: var(--stage);
    font-family: "Montserrat", sans-serif;
    position: relative;
  }
  .card {
    position: absolute;
    width: 560px;
    height: 330px;
    border-radius: 22px;
    overflow: hidden;
    background: var(--navy);
    box-shadow: 0 18px 40px rgba(0,0,0,.55);
  }
  .card--front { left: 60px; top: 80px; }
  .card--back { left: 580px; top: 510px; }

  .office-backdrop {
    position: absolute; inset: 0;
    background: linear-gradient(160deg, var(--navy) 0%, var(--navy-soft) 55%, var(--navy-deep) 100%);
    opacity: .9;
  }

  /* Front */
  .front-band { position: absolute; left: 0; bottom: 0; width: 100%; height: 110px; }
  .front-content {
    position: absolute; left: 0; right: 0; top: 46px;
    display: flex; flex-direction: column; align-items: center; text-align: center;
  }
  .brand { display: flex; align-items: center; gap: 10px; margin-bottom: 16px; }
  .brand__mark { width: 26px; height: 26px; background: var(--white); border-radius: 3px; }
  .brand__name { color: var(--white); font-weight: 800; font-size: 30px; letter-spacing: 1px; }
  .person-name { color: var(--gold); font-weight: 800; font-size: 24px; letter-spacing: .5px; margin-bottom: 10px; }
  .contact-item { display: flex; flex-direction: column; align-items: center; color: var(--white); font-size: 15px; font-weight: 500; line-height: 1.25; margin-bottom: 4px; }
  .contact-item svg { width: 16px; height: 16px; margin-bottom: 1px; }

  /* Back */
  .portrait {
    position: absolute;
    background: linear-gradient(180deg, #6b7090 0%, #2a2f45 100%);
  }
  .portrait--left { left: 60px; top: 120px; width: 180px; height: 210px; border-radius: 90px 90px 0 0; }
  .portrait--right { left: 420px; top: 34px; width: 140px; height: 252px; border-radius: 70px 70px 0 0; }
  .back-headline {
    position: absolute; left: 30px; right: 160px; top: 34px; text-align: center;
  }
  .firm-title { color: var(--gold); font-weight: 800; font-size: 26px; letter-spacing: .5px; white-space: nowrap; }
  .firm-title sup { font-size: 12px; font-weight: 500; }
  .callout {
    position: absolute; left: 240px; top: 78px; width: 160px;
    color: var(--white); font-weight: 800; font-size: 15px; line-height: 1.25; text-align: center;
  }
  .stat {
    position: absolute; left: 218px; top: 150px; width: 200px;
    color: var(--white); font-size: 12.5px; line-height: 1.4; text-align: center;
  }
  .cta {
    position: absolute; left: 222px; top: 205px; z-index: 2;
    background: var(--gold); color: var(--navy-deep);
    font-weight: 800; font-size: 10.5px; letter-spacing: .3px; white-space: nowrap;
    padding: 9px 14px; border-radius: 20px;
  }
  .back-band { position: absolute; left: 0; top: 0; width: 560px; height: 330px; z-index: 1; }
  .perk {
    position: absolute; z-index: 2; display: flex; align-items: center; gap: 6px;
    color: var(--navy-deep); font-weight: 500; white-space: nowrap; line-height: 1;
  }
  .perk__icon {
    flex: none;
    width: 22px; height: 22px; border-radius: 50%;
    background: var(--navy); border: 2px solid var(--gold);
    box-shadow: 0 0 0 2px var(--navy);
    display: flex; align-items: center; justify-content: center;
    color: var(--gold); font-size: 11px; font-weight: 700;
  }
  .perk--consult { left: 16px; top: 302px; font-size: 12.5px; }
  .perk--fee { left: 246px; top: 284px; font-size: 14px; }
  .perk--visit { left: 434px; top: 299px; font-size: 10.5px; gap: 5px; }
  .perk--visit .perk__icon { width: 16px; height: 16px; font-size: 7px; box-shadow: 0 0 0 1.5px var(--navy); }
</style>
</head>
<body>

<section class="card card--front">
  <div class="office-backdrop" role="img" aria-label="Muted photograph of a modern glass office interior"></div>
  <svg class="front-band" viewBox="0 0 560 110" preserveAspectRatio="none" aria-hidden="true">
    <path d="M0 110 L0 92 Q0 78 30 76 L560 20 L560 0 Q560 60 530 62 Z" fill="var(--gold)"/>
  </svg>
  <div class="front-content">
    <div class="brand">
      <span class="brand__mark"></span>
      <span class="brand__name">OAK PARTNERS</span>
    </div>
    <div class="person-name">DORIAN PEMBERTON</div>
    <div class="contact-item">
      <svg viewBox="0 0 24 24" fill="var(--gold)"><path d="M6.6 10.8a15 15 0 0 0 6.6 6.6l2.2-2.2c.3-.3.7-.4 1-.2 1.1.4 2.3.6 3.6.6.6 0 1 .4 1 1V20c0 .6-.4 1-1 1A17 17 0 0 1 3 4c0-.6.4-1 1-1h3.5c.6 0 1 .4 1 1 0 1.3.2 2.5.6 3.6.1.3 0 .7-.2 1z"/></svg>
      800-555-0147
    </div>
    <div class="contact-item">
      <svg viewBox="0 0 24 24" fill="var(--gold)"><path d="M2 5h20v14H2z"/><path d="M2 5l10 8 10-8" fill="none" stroke="var(--navy)" stroke-width="2"/></svg>
      dorian@oakpartners.example
    </div>
    <div class="contact-item">
      <svg viewBox="0 0 24 24"><circle cx="12" cy="12" r="10" fill="var(--gold)"/><path d="M2 12h20M12 2c3 3 3 17 0 20M12 2c-3 3-3 17 0 20" fill="none" stroke="var(--navy)" stroke-width="1.5"/></svg>
      www.oakpartners.example
    </div>
  </div>
</section>

<section class="card card--back">
  <div class="office-backdrop" role="img" aria-label="Muted photograph of a modern glass office interior"></div>
  <div class="portrait portrait--left" role="img" aria-label="Portrait of a smiling partner in a dark suit and striped tie"></div>
  <div class="portrait portrait--right" role="img" aria-label="Portrait of a smiling partner in a navy suit and dark tie"></div>

  <div class="back-headline">
    <div class="firm-title">THE OAK PARTNERS<sup>®</sup></div>
  </div>
  <div class="callout">INJURED?<br>CALL OAK<br>PARTNERS!</div>
  <div class="stat">Over $400,000,000<br>Recovered For Our Clients.</div>
  <div class="cta">GET A FREE CONSULTATION NOW</div>

  <svg class="back-band" viewBox="0 0 560 330" aria-hidden="true">
    <polygon points="0,296 212,296 212,330 0,330" fill="var(--gold)"/>
    <polygon points="230,268 418,268 428,286 560,286 560,330 220,330" fill="var(--gold)"/>
    <line x1="418" y1="268" x2="428" y2="286" stroke="var(--navy)" stroke-width="3"/>
  </svg>

  <div class="perk perk--consult">
    <span class="perk__icon">✓</span>Free Consultation
  </div>
  <div class="perk perk--fee">
    <span class="perk__icon">$</span>No Fee Unless You Win
  </div>
  <div class="perk perk--visit">
    <span class="perk__icon">●</span>We'll Come To You
  </div>
</section>

</body>
</html>
```